Local Flower Farm Needs Business Card Design

I need business cards designed for a flower farm based in Eudora, Kansas.
Business Info:
We are a local cut flower farm located in Eudora, Kansas, founded by Corinne Haldwick. What started as a passion for agriculture and search for more joy in daily life has blossomed into a small business dedicated to providing the community with beautiful, fresh, and sustainable flowers. We specialize in local, seasonal blooms, ensuring that every petal reflects the care and dedication we pour into our craft. Our mission is to deliver the highest quality flowers directly to our customers through local farmers markets and to florists who share our commitment to sustainability. Join us in celebrating the beauty of nature, one bloom at a time!
Contact Details:
Corinne Haldwick
Owner
Phone 913-555-0147
Facebook: Rosalind Thorpe Gardens
Instagram: @RosalindThorpeGardens
Website: RosalindThorpeGardens.example
Target Market(s)
Wholesale to Florists and Direct to Consumer via Farmers Market
Industry/Entity Type
Florist, Farm
Contact Information for Business Card
Name, Contact Info, Logo
Look and feel
Each slider illustrates characteristics of the customer's brand and the style your logo design should communicate.

```html
<!DOCTYPE html>
<html lang="en">
<head>
<meta charset="utf-8">
<title>Rosalind Thorpe Gardens — Business Card</title>
<link rel="stylesheet" href="https://fonts.googleapis.com/css2?family=Roboto:wght@400;700&family=Roboto+Condensed:wght@700&display=swap">
<style>
  :root {
    --ink-deep: #0e2f33;
    --teal: #1f6166;
    --paper: #ffffff;
    --backdrop: #e9ecec;
    --muted: #5d6b6c;
  }
  * { box-sizing: border-box; margin: 0; padding: 0; }
  html, body { width: 1200px; height: 900px; overflow: hidden; }
  body {
    background: var(--backdrop);
    font-family: "Roboto", Arial, sans-serif;
    display: flex; flex-direction: column; align-items: center; justify-content: center;
    gap: 40px;
  }
  .card {
    position: relative;
    width: 700px; height: 400px;
    border-radius: 28px;
    overflow: hidden;
    box-shadow: 0 6px 18px rgba(0,0,0,.15);
  }
  .card--front { background: var(--paper); }
  .card--back { background: var(--ink-deep); display: flex; align-items: center; justify-content: center; }
  .wave { position: absolute; inset: 0; width: 100%; height: 100%; }
  .identity { position: absolute; left: 48px; top: 34px; }
  .identity__name {
    font-family: "Roboto Condensed", Arial Narrow, sans-serif;
    font-weight: 700; font-size: 27px; letter-spacing: .5px;
    text-transform: uppercase; color: var(--ink-deep);
  }
  .identity__role { font-size: 14px; color: var(--muted); margin-top: 2px; }
  .contacts {
    position: absolute; left: 48px; top: 176px;
    list-style: none; color: var(--paper); font-size: 17px; line-height: 30px;
  }
  .contacts li { display: flex; align-items: center; gap: 10px; }
  .contacts svg { width: 13px; height: 13px; flex: none; }
  .brand {
    position: absolute; display: flex; flex-direction: column; align-items: center; gap: 12px;
    font-weight: 700; text-align: center; line-height: 1.2;
  }
  .brand__ring { border-radius: 50%; border: 2px solid currentColor; }
  .brand--front { right: 56px; top: 150px; width: 190px; color: var(--ink-deep); font-size: 18px; }
  .brand--front .brand__ring { width: 60px; height: 60px; }
  .brand--back { position: static; width: 240px; color: var(--paper); font-size: 22px; }
  .brand--back .brand__ring { width: 80px; height: 80px; }
</style>
</head>
<body>
  <section class="card card--front">
    <svg class="wave" viewBox="0 0 700 400" preserveAspectRatio="none" aria-hidden="true">
      <path d="M0,112 C150,92 250,110 320,200 C390,300 430,385 520,400 L0,400 Z" fill="var(--ink-deep)"/>
      <path d="M0,92 C160,70 268,92 340,190 C410,290 455,372 560,400" fill="none" stroke="var(--teal)" stroke-width="9"/>
    </svg>
    <div class="identity">
      <h1 class="identity__name">Corinne Haldwick</h1>
      <p class="identity__role">Owner</p>
    </div>
    <ul class="contacts">
      <li><svg viewBox="0 0 24 24"><path fill="currentColor" d="M6.6 10.8a15.1 15.1 0 0 0 6.6 6.6l2.2-2.2c.3-.3.7-.4 1-.2 1.1.4 2.3.6 3.6.6.6 0 1 .4 1 1V20c0 .6-.4 1-1 1A17 17 0 0 1 3 4c0-.6.4-1 1-1h3.5c.6 0 1 .4 1 1 0 1.3.2 2.5.6 3.6.1.3 0 .7-.2 1z"/></svg>913-555-0147</li>
      <li><svg viewBox="0 0 24 24"><circle cx="12" cy="12" r="10" fill="currentColor"/></svg>Rosalind Thorpe Gardens</li>
      <li><svg viewBox="0 0 24 24"><rect x="3" y="3" width="18" height="18" rx="5" fill="none" stroke="currentColor" stroke-width="2.5"/></svg>@RosalindThorpeGardens</li>
      <li><svg viewBox="0 0 24 24"><circle cx="12" cy="12" r="9" fill="none" stroke="currentColor" stroke-width="2.5"/></svg>RosalindThorpeGardens.example</li>
    </ul>
    <div class="brand brand--front">
      <span class="brand__ring"></span>
      <span class="brand__name">Rosalind Thorpe Gardens</span>
    </div>
  </section>

  <section class="card card--back">
    <div class="brand brand--back">
      <span class="brand__ring"></span>
      <span class="brand__name">Rosalind Thorpe Gardens</span>
    </div>
  </section>
</body>
</html>
```